Meridale Staffing Website

My business has been word of mouth over the last 3 years and has grown. Now I need a website for additional marketing as we have new clients asking for a website.

You have already completed my Logo during an earlier project. I have attached the logo.

We do Staff Augmentation and Operation Support.

What is that?
Staff augmentation is an outsourcing strategy that allows companies to fill specific, temporary roles to achieve business objectives. This staffing method complements existing teams with specific talent, enhancing business capabilities or filling gaps left by members on extended leave.

We work alongside the internal recruiting team to assist clients to meet and exceed financial goals.

```html
<!DOCTYPE html>
<html lang="en">
<head>
<meta charset="utf-8">
<title>Meridale Staffing</title>
<link href="https://fonts.googleapis.com/css2?family=PT+Sans:wght@400;700&family=Arimo:wght@400;700&display=swap" rel="stylesheet">
<style>
:root{
  --navy:#0d3f6b;
  --navy-deep:#0a3258;
  --blue:#0b4a7d;
  --ink:#222;
  --muted:#444;
  --grey-bar:#7d7d7d;
  --hero-a:#e4e3e8;
  --hero-b:#cfcdd6;
  --panel:#e7e7e7;
  --gold:#d9a21b;
  --white:#fff;
}
*{margin:0;padding:0;box-sizing:border-box}
html,body{width:1200px;height:5195px;overflow:hidden}
body{position:relative;background:var(--white);font-family:"Arimo",Arial,sans-serif;color:var(--ink)}
.abs{position:absolute}
h1,h2,h3,.head{font-family:"PT Sans",Arial,sans-serif;font-weight:700}
.btn{position:absolute;display:flex;align-items:center;gap:10px;padding-left:14px;font-family:"PT Sans",sans-serif;font-weight:700;font-size:14px;color:var(--white);background:var(--navy);border-radius:3px;text-transform:uppercase}
.btn .dot{width:22px;height:22px;border-radius:50%;border:3px solid var(--white)}
.btn.outline{background:transparent;border:3px solid var(--white);border-radius:6px}
.ph{position:absolute}
/* top bar */
.topbar{top:0;left:0;width:1200px;height:50px;background:var(--navy)}
.topbar .email{position:absolute;left:0;top:0;width:440px;height:50px;background:var(--grey-bar);clip-path:polygon(0 0,100% 0,94% 100%,0 100%);color:#fff;font-size:15px;line-height:50px;padding-left:127px}
.topbar .call{position:absolute;left:741px;top:0;line-height:46px;color:#fff;font-size:15px}
.social{display:flex;gap:22px;position:absolute}
.social span{width:12px;height:12px;border-radius:50%;background:#fff}
/* nav */
.brand{display:flex;align-items:center;gap:10px;position:absolute;font-family:"PT Sans",sans-serif;font-weight:700;color:var(--navy)}
.brand .mark{border-radius:50%;background:var(--navy)}
.nav a{position:absolute;top:76px;font-size:15px;color:#333;text-decoration:none}
.nav a.active{color:var(--navy);font-weight:700;border-bottom:2px solid var(--navy);padding-bottom:4px}
.login{position:absolute;left:986px;top:67px;width:101px;height:38px;background:var(--navy);color:#fff;font-family:"PT Sans",sans-serif;font-weight:700;font-size:15px;display:flex;align-items:center;justify-content:center;border-radius:2px}
.arrow{position:absolute;width:30px;height:30px;border-radius:50%;display:flex;align-items:center;justify-content:center}
/* common */
.para{position:absolute;font-size:15px;line-height:25px;color:var(--ink)}
.section-title{position:absolute;left:0;width:1200px;text-align:center;font-size:29px;color:var(--navy)}
.card{position:absolute;top:2888px;width:222px;height:333px;background:#fff;box-shadow:0 2px 10px rgba(0,0,0,.2);text-align:center}
.card .avatar{position:absolute;left:36px;top:28px;width:150px;height:150px;border-radius:50%;border:3px solid var(--navy);overflow:hidden}
.card .avatar div{width:100%;height:100%}
.card .name{position:absolute;top:196px;width:100%;font-family:"PT Sans",sans-serif;font-weight:700;font-size:19px;color:var(--blue)}
.card .role{position:absolute;top:230px;width:100%;font-size:18px;color:var(--blue)}
.card .icons{position:absolute;top:268px;left:36px;display:flex;gap:14px}
.card .icons span{width:26px;height:26px;border-radius:50%;border:2px solid var(--navy)}
.card.featured{background:var(--navy)}
.card.featured .name,.card.featured .role{color:#fff}
.card.featured .avatar,.card.featured .icons span{border-color:#fff}
.partner{position:absolute;top:4188px;width:96px;height:96px;border-radius:50%;background:#fff;box-shadow:0 3px 12px rgba(0,0,0,.18);display:flex;align-items:center;justify-content:center}
.partner i{display:block;width:48px;height:48px;border-radius:50%;background:var(--blue);opacity:.85}
.field{position:absolute;height:44px;background:#fff;border:1px solid #ddd;font-size:12px;color:#333;display:flex;align-items:center;gap:10px;padding-left:24px}
.field b{width:10px;height:10px;background:#333;border-radius:2px}
.foot-h{position:absolute;font-family:"PT Sans",sans-serif;font-weight:700;font-size:16px;color:#fff}
.foot-list{position:absolute;list-style:none;color:#fff;font-size:14px;line-height:25px}
.contact-row{position:absolute;left:868px;display:flex;align-items:center;gap:12px;color:#fff;font-size:14px}
.contact-row span{width:26px;height:26px;border-radius:50%;border:2px solid #fff;flex:none}
</style>
</head>
<body>

<!-- top bar -->
<div class="abs topbar">
  <div class="email"><b>Email :</b> hello@meridalestaffing.com</div>
  <div class="call"><b>Call Us:</b> &nbsp;+1 555 014 2290</div>
  <div class="social" style="left:955px;top:19px"><span></span><span></span><span></span><span></span></div>
</div>

<!-- navigation -->
<div class="brand" style="left:111px;top:62px;font-size:24px"><span class="mark" style="width:42px;height:42px"></span>Meridale Staffing</div>
<nav class="nav">
  <a class="active" style="left:466px">Home</a>
  <a style="left:552px">About</a>
  <a style="left:637px">Our Services</a>
  <a style="left:766px">Testimonials</a>
  <a style="left:895px">Contact</a>
</nav>
<div class="login">LOG IN</div>

<!-- hero -->
<section class="abs" style="left:0;top:121px;width:1200px;height:641px;background:linear-gradient(90deg,var(--hero-a),var(--hero-b))">
  <div class="ph" role="img" aria-label="Smiling woman in glasses holding a tablet" style="left:40px;top:30px;width:600px;height:611px;background:radial-gradient(ellipse at 45% 55%,#b89c8a 0%,#d7d3d8 60%,transparent 75%)"></div>
  <svg class="abs" style="left:0;top:590px" width="1200" height="52"><path d="M0 52 L1100 52 Q1150 35 1200 52 Z" fill="#fff"/></svg>
  <h1 class="abs" style="left:656px;top:188px;font-size:44px;line-height:56px;color:#111">WELCOME TO<br><span style="color:var(--navy)">MERIDALE STAFFING</span></h1>
  <p class="para" style="left:656px;top:302px;width:440px;font-size:14px;line-height:25px;color:#333">Lorem ipsum dolor sit amet, consectetur adipiscing elit, sed do eiusmod tempor incididunt ut labore et dolore magna aliqua. Ut enim ad minim veniam, quis .</p>
  <div class="btn" style="left:657px;top:395px;width:154px;height:47px"><span class="dot"></span>Get Started</div>
  <div class="btn" style="left:825px;top:395px;width:153px;height:47px"><span class="dot"></span>Learn More</div>
  <div class="arrow" style="left:40px;top:316px;background:var(--navy)"><svg width="10" height="10"><path d="M7 1 L3 5 L7 9" stroke="#fff" stroke-width="2" fill="none"/></svg></div>
  <div class="arrow" style="left:1123px;top:316px;background:var(--navy)"><svg width="10" height="10"><path d="M3 1 L7 5 L3 9" stroke="#fff" stroke-width="2" fill="none"/></svg></div>
</section>

<!-- about -->
<h2 class="abs" style="left:111px;top:904px;font-size:30px;color:#111">ABOUT <span style="color:var(--navy)">MERIDALE STAFFING</span></h2>
<p class="para" style="left:111px;top:954px;width:490px;font-size:14px;line-height:28px">Lorem ipsum dolor sit amet, consectetur adipiscing elit, sed do eiusmod tempor incididunt ut labore et dolore magna aliqua. Ut enim ad minim veniam, quis nostrud exercitation ullamco laboris nisi ut aliquip ex ea commodo consequat.Duis aute irure dolor in reprehenderit in voluptate velit esse cillum dolore eu fugiat nulla pariatur. Excepteur sint occaecat cupidatat non proident, sunt in culpa qui officia deserunt mollit anim id est laborum.</p>
<div class="btn" style="left:111px;top:1168px;width:152px;height:46px"><span class="dot"></span>Read More</div>
<svg class="abs" style="left:676px;top:833px" width="420" height="462">
  <rect x="101" y="0" width="312" height="462" fill="var(--navy)"/>
  <g fill="#111">
    <circle cx="4" cy="4" r="3"/><circle cx="22" cy="4" r="3"/><circle cx="40" cy="4" r="3"/><circle cx="58" cy="4" r="3"/><circle cx="76" cy="4" r="3"/>
    <circle cx="4" cy="22" r="3"/><circle cx="22" cy="22" r="3"/><circle cx="40" cy="22" r="3"/><circle cx="58" cy="22" r="3"/><circle cx="76" cy="22" r="3"/>
    <circle cx="4" cy="420" r="3"/><circle cx="22" cy="420" r="3"/><circle cx="40" cy="420" r="3"/><circle cx="58" cy="420" r="3"/><circle cx="76" cy="420" r="3"/>
    <circle cx="4" cy="440" r="3"/><circle cx="22" cy="440" r="3"/><circle cx="40" cy="440" r="3"/><circle cx="58" cy="440" r="3"/><circle cx="76" cy="440" r="3"/>
  </g>
</svg>
<div class="ph" role="img" aria-label="Two business people in a meeting" style="left:688px;top:871px;width:359px;height:386px;background:linear-gradient(135deg,#cfd3d6,#5f646a 60%,#2c2f35)"></div>

<!-- services -->
<svg class="abs" style="left:0;top:1378px" width="1200" height="1300"><path d="M0 0 L1130 0 Q1200 0 1200 60 L1200 1310 L1130 1290 L60 1290 Q0 1290 0 1230 Z" fill="var(--navy)"/></svg>
<h2 class="section-title" style="top:1478px;color:#fff">OUR SERVICES</h2>

<svg class="abs" style="left:130px;top:1612px" width="420" height="420"><path d="M8 395 L8 8 L340 8" stroke="#fff" stroke-width="3" fill="none"/><path d="M420 60 L420 395" stroke="#fff" stroke-width="3" fill="none"/></svg>
<div class="ph" role="img" aria-label="Smiling woman reaching out for a handshake in an office" style="left:113px;top:1638px;width:409px;height:379px;background:linear-gradient(120deg,#c9d2da,#d89a8a 45%,#6a7680)"></div>
<div class="abs" style="left:467px;top:1588px;width:114px;height:114px;border-radius:50%;background:#fff;border:4px solid var(--navy);display:flex;align-items:center;justify-content:center"><svg width="48" height="48"><circle cx="24" cy="15" r="10" fill="var(--navy)"/><path d="M6 46 Q24 22 42 46 Z" fill="var(--navy)"/></svg></div>
<h3 class="abs" style="left:617px;top:1702px;font-size:28px;color:#fff">Staff Augmentation</h3>
<p class="para" style="left:617px;top:1752px;width:470px;font-size:14px;line-height:25px;color:#fff;text-align:justify">Lorem ipsum dolor sit amet, consectetur adipiscing elit, sed do eiusmod tempor incididunt ut labore et dolore magna aliqua. Ut enim ad minim veniam, quis nostrud exercitation ullamco laboris nisi ut aliquip ex ea commodo consequat.Duis aute irure dolor in reprehenderit in voluptate velit esse cillum dolore</p>
<div class="btn outline" style="left:608px;top:1904px;width:157px;height:51px"><span class="dot"></span>Read More</div>

<h3 class="abs" style="left:111px;top:2176px;font-size:28px;color:#fff">Operation Support</h3>
<p class="para" style="left:111px;top:2226px;width:470px;font-size:14px;line-height:25px;color:#fff;text-align:justify">Lorem ipsum dolor sit amet, consectetur adipiscing elit, sed do eiusmod tempor incididunt ut labore et dolore magna aliqua. Ut enim ad minim veniam, quis nostrud exercitation ullamco laboris nisi ut aliquip ex ea commodo consequat.Duis aute irure dolor in reprehenderit in voluptate velit esse cillum dolore</p>
<div class="btn outline" style="left:109px;top:2375px;width:157px;height:51px"><span class="dot"></span>Read More</div>
<svg class="abs" style="left:640px;top:2086px" width="446" height="384"><path d="M80 3 L420 3 Q443 3 443 26 L443 380 L380 380" stroke="#fff" stroke-width="3" fill="none"/></svg>
<div class="ph" role="img" aria-label="Technician with a laptop in a server room" style="left:647px;top:2112px;width:408px;height:375px;border-radius:24px 0 0 0;background:linear-gradient(100deg,#0e1a16,#1f5a3a 40%,#6d8a96 70%,#263238)"></div>
<div class="abs" style="left:600px;top:2042px;width:114px;height:114px;border-radius:50%;background:#fff;border:4px solid var(--navy);display:flex;align-items:center;justify-content:center"><svg width="50" height="50"><circle cx="18" cy="12" r="8" fill="var(--navy)"/><rect x="8" y="22" width="20" height="24" rx="4" fill="var(--navy)"/><circle cx="36" cy="34" r="10" fill="none" stroke="var(--navy)" stroke-width="5"/></svg></div>

<!-- team -->
<h2 class="section-title" style="top:2780px">MEET THE TEAM</h2>
<div class="card" style="left:111px"><div class="avatar"><div role="img" aria-label="Portrait of team member" style="background:linear-gradient(#c7cdd2,#9b7a5f)"></div></div><div class="name">JHON LEE</div><div class="role">Lorem ipsum dolor</div><div class="icons"><span></span><span></span><span></span><span></span></div></div>
<div class="card" style="left:363px"><div class="avatar"><div role="img" aria-label="Portrait of team member" style="background:linear-gradient(#d9c6b7,#8a5f45)"></div></div><div class="name">JHON LEE</div><div class="role">Lorem ipsum dolor</div><div class="icons"><span></span><span></span><span></span><span></span></div></div>
<div class="card featured" style="left:615px"><div class="avatar"><div role="img" aria-label="Portrait of team member" style="background:linear-gradient(#e8e8e8,#3c3f46)"></div></div><div class="name">JHON LEE</div><div class="role">Lorem ipsum dolor</div><div class="icons"><span></span><span></span><span></span><span></span></div></div>
<div class="card" style="left:867px"><div class="avatar"><div role="img" aria-label="Portrait of team member" style="background:linear-gradient(#b9d3e3,#5d4334)"></div></div><div class="name">JHON LEE</div><div class="role">Lorem ipsum dolor</div><div class="icons"><span></span><span></span><span></span><span></span></div></div>

<!-- testimonials -->
<svg class="abs" style="left:0;top:3290px" width="1200" height="720"><path d="M0 18 L1140 18 L1200 0 L1200 660 Q1200 714 1146 714 L60 714 Q20 714 0 700 Z" fill="var(--navy)"/></svg>
<h2 class="section-title" style="top:3394px;color:#fff">OUR TESTIMONIALS</h2>
<div class="abs" style="left:228px;top:3858px;width:724px;height:22px;background:#ccc"></div>
<div class="abs" style="left:218px;top:3858px;width:744px;height:12px;background:#e2e2e2"></div>
<div class="abs" style="left:210px;top:3493px;width:760px;height:365px;background:#fff;text-align:center">
  <div role="img" aria-label="Portrait of client" style="position:absolute;left:340px;top:36px;width:80px;height:80px;border-radius:50%;background:linear-gradient(#e9e9e9,#8e2a2a)"></div>
  <div class="head" style="position:absolute;top:144px;width:100%;font-size:18px;color:var(--blue)">JHONY WARD</div>
  <div style="position:absolute;top:176px;width:100%;font-size:19px;color:#222">Lorem ipsum dolor</div>
  <p style="position:absolute;left:52px;top:218px;width:656px;font-size:14px;line-height:30px;color:#444">Lorem ipsum dolor sit amet, consectetur adipiscing elit, sed do eiusmod tempor incididunt ut labore et dolore magna aliqua. Ut enim ad minim veniam, quis nostrud exercitation ullamco laboris nisi ut aliquip ex ea commodo consequatLorem ipsum dolor</p>
  <div style="position:absolute;top:312px;width:100%;font-size:18px;letter-spacing:3px;color:var(--gold)">★★★★★</div>
</div>
<div class="arrow" style="left:41px;top:3638px;background:#fff"><svg width="10" height="10"><path d="M7 1 L3 5 L7 9" stroke="var(--navy)" stroke-width="2" fill="none"/></svg></div>
<div class="arrow" style="left:1126px;top:3638px;background:#fff"><svg width="10" height="10"><path d="M3 1 L7 5 L3 9" stroke="var(--navy)" stroke-width="2" fill="none"/></svg></div>

<!-- partners -->
<h2 class="section-title" style="top:4092px;color:#111">OUR <span style="color:var(--navy)">PARTNER</span></h2>
<div class="partner" style="left:111px"><i></i></div>
<div class="partner" style="left:287px"><i></i></div>
<div class="partner" style="left:462px"><i></i></div>
<div class="partner" style="left:640px"><i></i></div>
<div class="partner" style="left:817px"><i></i></div>
<div class="partner" style="left:995px"><i></i></div>

<!-- footer band -->
<svg class="abs" style="left:0;top:4720px" width="1200" height="475"><path d="M0 0 L40 20 L1200 20 L1200 475 L0 475 Z" fill="var(--navy)"/></svg>

<!-- contact -->
<section class="abs" style="left:236px;top:4373px;width:730px;height:454px;background:var(--panel)">
  <h3 class="abs" style="left:0;top:48px;width:100%;text-align:center;font-size:18px;color:var(--navy)">CONTACT US</h3>
</section>
<div class="field" style="left:315px;top:4488px;width:274px"><b></b>Frist Name</div>
<div class="field" style="left:617px;top:4488px;width:272px"><b></b>Last Name</div>
<div class="field" style="left:315px;top:4560px;width:274px"><b></b>Email Address</div>
<div class="field" style="left:617px;top:4560px;width:272px"><b></b>Phone Number</div>
<div class="field" style="left:315px;top:4635px;width:566px;height:62px"><b></b>Message........</div>
<div class="abs" style="left:530px;top:4732px;width:140px;height:42px;background:var(--navy);color:#fff;font-family:'PT Sans',sans-serif;font-weight:700;font-size:14px;display:flex;align-items:center;justify-content:center;border-radius:2px">SUBMIT</div>

<!-- footer -->
<div class="brand" style="left:111px;top:4918px;font-size:27px;color:#fff"><span class="mark" style="width:50px;height:50px;background:#fff"></span>Meridale Staffing</div>
<p class="para" style="left:111px;top:4992px;width:240px;font-size:14px;line-height:25px;color:#fff;text-align:justify">Lorem ipsum dolor sit amet, consectetur adipiscing elit, sed do eiusmod tempor incididunt ut labore</p>
<div class="foot-h" style="left:447px;top:4908px">USE LINK</div>
<ul class="foot-list" style="left:450px;top:4942px"><li><b>Home</b></li><li>About</li><li>Our Services</li><li>Testimonials</li><li>Contact</li></ul>
<div class="foot-h" style="left:651px;top:4910px">HELP LINK</div>
<ul class="foot-list" style="left:653px;top:4942px;line-height:33px"><li>Terms&amp;condtions</li><li>Privacy Policy</li><li>Support</li><li>Blog</li></ul>
<div class="foot-h" style="left:875px;top:4906px">Contact Us</div>
<div class="contact-row" style="top:4943px"><span></span>555 014 2290</div>
<div class="contact-row" style="top:4985px"><span></span>hello@meridalestaffing.com</div>
<div class="contact-row" style="top:5026px"><span></span>90 Lorem ipsum dolor</div>
<div class="abs" style="left:111px;top:5133px;display:flex;gap:14px"><span style="width:30px;height:30px;border-radius:50%;border:2px solid #fff"></span><span style="width:30px;height:30px;border-radius:50%;border:2px solid #fff"></span><span style="width:30px;height:30px;border-radius:50%;border:2px solid #fff"></span><span style="width:30px;height:30px;border-radius:50%;border:2px solid #fff"></span></div>
<div class="abs" style="left:447px;top:5138px;color:#fff;font-size:14px">©Copyrights 2022 Meridale Staffing | All Rights Reserved</div>

</body>
</html>
```